Martial Arts Website

Redevelopment of existing martial arts website.

The academy teaches traditional shaolin martial arts, including Shaolin Kung Fu, Wu Shu, Tai Chi, Qigong and Wing Chun and the site needs to reflect the traditional roots (eg, no tacky boxing imagery)

Existing website is www.copperlantern.com.au to get a feel for the desired color scheme (black, green and red). The exact colors can be tweaked though. Please only reuse the logo and font (Karate) - there isnt anything else from the current design that needs to remain.

The current website includes links to a ClipHarbor channel that includes demonstrations of the training conducted to better guide the design.

The new website site map will be:
1. Home
2. Programs - summary page describing each form of training
a. Tiny Otters
b. Kids Kung Fu
c. Youth Kung Fu
d. Adults Kung Fu
e. Wing Chun
f. Tai Chi & Qigong
g. Weaponry Classes
h. 72 Arts of Shaolin Conditioning Program
i. Acrobatics and Wu Shu
j. Fitness Boxing
3. Timetable
4. Coaches - summary page describing all coaches
a. Sifu (Master)
b. Sihing Kit
c. Sihing Sam
d. Sihing Marcus
X. ... up to 10 or so coaches
5. Member Zone
6. Contact Us
Updates

Logo now attached to brief - sorry I only have it in PDF

Just to clarify, I am only expecting a PSD design - no HTML required

Reason: Thanks for the designs, we love a lot of them just require a little extra time to tweak the designs and establish the potential. Thanks for your understanding and efforts.

Target Market(s)

Parents, teenagers, young adults, adults, elderly

Industry/Entity Type

Training

Requirements
Must have
• Chinese kung fu dragon imagery throughout the background
Links to Chatterly and ClipHarbor channel
Promo/icon in the header "Try 2 free classes now"
Home page should include an embedded ClipHarbor video

```html
<!DOCTYPE html>
<html lang="en">
<head>
<meta charset="utf-8">
<title>Copper Lantern Martial Arts Academy</title>
<link href="https://fonts.googleapis.com/css2?family=Arimo:wght@400;700&display=swap" rel="stylesheet">
<style>
:root{
  --bg:#000;
  --green-top:#8ee86f;
  --green-bot:#4fb83a;
  --green-dark:#3f8f33;
  --green-text:#5ccf4a;
  --red-top:#f0545a;
  --red-bot:#c41a22;
  --red-text:#e0262e;
  --nav-text:#0c1a08;
  --body-text:#cfcfcf;
  --muted:#5a5a5a;
  --frame:#6a6a6a;
}
*{margin:0;padding:0;box-sizing:border-box}
html,body{width:1200px;height:1109px;overflow:hidden;background:var(--bg)}
body{position:relative;font-family:"Arimo",Arial,sans-serif;color:var(--body-text)}
.backdrop{position:absolute;inset:0;background:
  radial-gradient(ellipse 260px 420px at 1110px 320px,rgba(60,60,60,.35),transparent 70%),
  radial-gradient(ellipse 220px 420px at 40px 760px,rgba(60,60,60,.3),transparent 70%)}
.brand{position:absolute;left:29px;top:8px;width:126px;height:126px;border-radius:50%;
  border:5px solid var(--green-bot);background:#0b1a08;display:flex;align-items:center;justify-content:center;
  text-align:center;font-size:13px;line-height:16px;color:var(--green-text);padding:14px}
.social{position:absolute;right:30px;top:66px;display:flex;gap:10px;font-size:11px;color:var(--body-text)}
.nav{position:absolute;left:27px;top:140px;width:1144px;height:49px;
  background:linear-gradient(var(--green-top),var(--green-bot));display:flex}
.nav a{display:flex;align-items:center;justify-content:center;color:var(--nav-text);text-decoration:none;
  font-size:16px;letter-spacing:.5px;border-right:1px solid rgba(0,0,0,.15)}
.nav a.home{color:#fff}
.nav a.active{background:var(--green-dark);color:#1a3a12}
.cta{position:absolute;left:937px;top:146px;width:222px;height:38px;
  background:linear-gradient(var(--red-top),var(--red-bot));border:1px solid #7a1015;
  color:#5a0a0c;font-size:15px;display:flex;align-items:center;justify-content:center;letter-spacing:.3px}
.hero{position:absolute;left:27px;top:189px;width:1144px;height:425px;
  background:linear-gradient(#4a6a85 0%,#b9a28a 40%,#f08a2a 62%,#c85a1a 78%,#5a5a6a 100%)}
.dropdown{position:absolute;left:145px;top:189px;width:187px;background:rgba(74,150,60,.85);list-style:none}
.dropdown li{height:32.7px;line-height:32.7px;padding-left:16px;font-size:14px;color:#0e1e0a;
  border-bottom:1px solid rgba(255,255,255,.2)}
.programs{position:absolute;left:28px;top:623px;display:flex;gap:6px}
.tile{width:122px;height:90px;border:1px solid #2c5c22;background:linear-gradient(var(--green-top),var(--green-bot));
  display:flex;flex-direction:column;align-items:center;justify-content:center;text-align:center;
  color:#0d1a08;font-size:14px;line-height:18px}
.tile b{font-weight:400;color:#fff;font-size:16px;line-height:23px}
.tile span{color:#eaffe0;font-size:15px}
.tile.featured{background:linear-gradient(var(--red-top),var(--red-bot));border-color:#7a1015}
.welcome{position:absolute;left:29px;top:742px;width:690px}
.welcome h1{font-weight:400;font-size:24px;color:var(--green-text);margin-bottom:12px}
.welcome p{font-size:15px;line-height:23.3px}
.more{position:absolute;left:613px;top:939px;color:var(--red-text);font-size:14px}
.video{position:absolute;left:798px;top:738px;width:372px;height:216px;border:3px solid var(--frame);background:#000}
.video svg{position:absolute;left:0;top:0}
.rule{position:absolute;left:28px;top:1015px;width:1143px;height:1px;background:var(--frame)}
.footer{position:absolute;left:0;top:1046px;width:1200px;text-align:center;font-size:12px;line-height:19px;color:var(--muted)}
</style>
</head>
<body>
<div class="backdrop" role="img" aria-label="Faint dragon artwork in the background"></div>
<div class="brand">Copper Lantern</div>
<div class="social"><span>Chirpline</span><span>ClipHarbor</span><span>Chatterly</span></div>

<div class="hero" role="img" aria-label="Silhouette of a martial artist with a sword against an orange sunset above the clouds"></div>

<nav class="nav">
  <a class="home" style="width:118px">Home</a>
  <a class="active" style="width:137px">Programs</a>
  <a style="width:138px">Timetable</a>
  <a style="width:127px">Coaches</a>
  <a style="width:170px">Member Zone</a>
  <a style="width:151px">Contact Us</a>
</nav>
<div class="cta">TRY TWO FREE CLASSES</div>

<ul class="dropdown">
  <li>a. Tiny Otters</li><li>b. Kids Kung Fu</li><li>c. Youth Kung Fu</li><li>d. Adults Kung Fu</li>
  <li>e. Wing Chun</li><li>f. Tai Chi &amp; Qigong</li><li>g. Weaponry Classes</li><li>h. 72 Arts of Shaolin</li>
</ul>

<div class="programs">
  <div class="tile featured">Tiny Otters<b>Ages</b><b>4 to 6</b></div>
  <div class="tile">Kids Kung Fu<b>Ages</b><b>6 to 11</b></div>
  <div class="tile">Youth Kung Fu<b>Ages</b><b>11 to 15</b></div>
  <div class="tile">Adults Kung Fu<b>Ages</b><b>15 &amp; over</b></div>
  <div class="tile">Wing Chun<b>Ages</b><b>13 &amp; over</b></div>
  <div class="tile">Tai Chi &amp;<br>Qigong<span>All ages</span></div>
  <div class="tile">Weaponry<br>Classes<b>Ages</b><b>5 &amp; over</b></div>
  <div class="tile">72 Arts of<br>Shaolin<span>Conditioning<br>Program</span></div>
  <div class="tile">Performance<br>Team<span>Acrobatics &amp;<br>Wu Shu</span></div>
</div>

<section class="welcome">
  <h1>Welcome to Copper Lantern Martial Arts Academy</h1>
  <p>Copper Lantern Martial Arts Academy is a purpose built (design and fitted), traditional martial arts centre providing professional, quality instruction in martial arts for all ages and physical capabilities. Our mission is to provide a high energy, motivating, safe environment with expert, practical instruction that will give you attention and progress. You will be welcomed into our traditional style centre, feel enthusiastic about achieving your personal goals and reaching your true potential as a martial artist. Traditional martial arts' training develops the mind, body and spirit.</p>
</section>
<div class="more">READ MORE</div>

<div class="video">
  <svg width="366" height="210" viewBox="0 0 366 210">
    <polygon points="178,88 178,104 190,96" fill="#777"/>
    <rect x="8" y="182" width="350" height="18" fill="#3a3a3a"/>
    <rect x="14" y="189" width="338" height="4" fill="#111"/>
    <circle cx="27" cy="191" r="5" fill="#e0262e"/>
  </svg>
</div>

<div class="rule"></div>
<footer class="footer">
  Copyright © 2012 - Copper Lantern Martial Arts Pty Ltd. Kung Fu and Tai Chi Training Centre<br>
  Unit 9, 27 Harbour Lane, West Marlow NSW 2791
</footer>
</body>
</html>
```